Black Car Limousine transportation business in Naples Florida

Always stand for my reliability and RVD stands for Love, K and M are the first initials of my children's names. It should show professionalism and a dedication to customer service. We keep our clients identities private. Show our professionalism. We are Black car Black tie company. We service transportation on a reserve basis to and from residents, airports, casinos, hotels,

Target Market(s)

It is a Private car service. High end clients. Businesses, Celebrity and athletes. Service to airports, hotels, special events.

Industry/Entity Type

Business

Contact Information for Business Card

A pearl metallic or Luster card. Standard business card size. Would like the name, Company email, show we take credit cards and phone number. Currently I don't have a website but will like to add later.

Logo Text

STEADFAST RVD TRANSPORTATION

Font styles to use
Serif

Colors
eaeaea
000000

Requirements
Must have
• Must have Company email, show we take credit cards and phone number. Currently I don't have a website but will like to add later.
Nice to have
• Would like to stay with a black and white theme. Open to some color trim.
Should not have
• Open to suggestions

```html
<!DOCTYPE html>
<html lang="en">
<head>
<meta charset="utf-8">
<title>Steadfast RVD Transportation – Business Card</title>
<link href="https://fonts.googleapis.com/css2?family=Open+Sans:ital,wght@0,400;0,600;1,700&display=swap" rel="stylesheet">
<style>
  :root {
    --backdrop: #b8b8b8;
    --card: #ffffff;
    --ink: #000000;
    --text: #1a1a1a;
    --muted: #4a4a4a;
    --logo-grey: #8c8c8c;
    --car-dark: #161616;
    --car-light: #5a5a5a;
  }
  * { margin: 0; padding: 0; box-sizing: border-box; }
  html, body {
    width: 1105px;
    height: 1200px;
    overflow: hidden;
    background: var(--backdrop);
    font-family: "Open Sans", Arial, sans-serif;
    color: var(--text);
  }
  .stage { position: relative; width: 1105px; height: 1200px; }
  .card {
    position: absolute;
    left: 193px;
    width: 720px;
    height: 412px;
    background: var(--card);
    overflow: hidden;
  }
  .card--front { top: 167px; }
  .card--back { top: 623px; }

  .side-band {
    position: absolute; left: 0; top: 0;
    width: 123px; height: 100%;
    background: var(--ink);
  }
  .brand-car {
    position: absolute; left: 46px; top: 100px;
    width: 138px; height: 57px;
    border-radius: 14px 18px 8px 8px;
    background: linear-gradient(180deg, var(--car-light), var(--car-dark) 55%, #000);
  }
  .brand-name {
    position: absolute; left: 193px; top: 100px;
    font-weight: 600;
    font-size: 22px;
    line-height: 28px;
    letter-spacing: 1px;
    color: var(--logo-grey);
  }
  .brand-name span { display: block; font-size: 15.5px; letter-spacing: 1.6px; }

  .person { position: absolute; left: 192px; top: 208px; }
  .person__name { font-weight: 600; font-size: 25px; line-height: 30px; color: var(--ink); }
  .person__title { font-size: 19px; line-height: 26px; color: var(--muted); }

  .contact { position: absolute; left: 192px; top: 278px; list-style: none; }
  .contact li {
    display: flex; align-items: center;
    height: 27.5px;
    font-size: 19px;
    color: var(--muted);
  }
  .contact svg { width: 18px; height: 18px; margin-right: 10px; fill: var(--ink); flex: none; }

  .feature-car {
    position: absolute; left: 152px; top: 129px;
    width: 387px; height: 156px;
    border-radius: 40px 70px 24px 24px;
    background: linear-gradient(180deg, #3a3a3a, var(--car-dark) 45%, #000 100%);
  }
  .payment-note {
    position: absolute; left: 0; right: 0; top: 334px;
    display: flex; justify-content: center; align-items: center;
    font-weight: 700; font-style: italic;
    font-size: 19px; color: var(--ink);
  }
  .payment-note svg { width: 30px; height: 20px; margin-right: 8px; }
</style>
</head>
<body>
<main class="stage">
  <section class="card card--front" aria-label="Business card front">
    <div class="side-band"></div>
    <div class="brand-car" role="img" aria-label="Photo of a black luxury SUV"></div>
    <div class="brand-name">STEADFAST RVD<span>TRANSPORTATION</span></div>
    <div class="person">
      <h1 class="person__name">JORDAN AVERY</h1>
      <p class="person__title">CEO/Founder</p>
    </div>
    <ul class="contact">
      <li>
        <svg viewBox="0 0 24 24" aria-hidden="true"><path d="M6.6 10.8a15.1 15.1 0 0 0 6.6 6.6l2.2-2.2c.3-.3.7-.4 1-.2 1.1.4 2.3.6 3.6.6.6 0 1 .4 1 1V20c0 .6-.4 1-1 1A17 17 0 0 1 3 4c0-.6.4-1 1-1h3.5c.6 0 1 .4 1 1 0 1.3.2 2.5.6 3.6.1.3 0 .7-.2 1z"/></svg>
        555 014 2760
      </li>
      <li>
        <svg viewBox="0 0 24 24" aria-hidden="true"><path d="M3 5h18v14H3z M4 6.5v.6l8 5.2 8-5.2v-.6z" fill-rule="evenodd"/></svg>
        hello@steadfastrvd.com
      </li>
      <li>
        <svg viewBox="0 0 24 24" aria-hidden="true"><circle cx="12" cy="12" r="10"/><path d="M7 6c2 1 3 3 2 5s1 3 3 3 1 3 0 5M14 4c0 2 2 3 4 3" stroke="#fff" stroke-width="1.6" fill="none"/></svg>
        www.steadfastrvd.com
      </li>
    </ul>
  </section>

  <section class="card card--back" aria-label="Business card back">
    <div class="feature-car" role="img" aria-label="Photo of a black luxury SUV, side three-quarter view"></div>
    <p class="payment-note">
      <svg viewBox="0 0 30 20" aria-hidden="true">
        <rect x="1" y="1" width="28" height="18" rx="3" fill="var(--ink)"/>
        <rect x="1" y="5" width="28" height="3" fill="#fff"/>
        <rect x="5" y="12" width="8" height="3" fill="#fff"/>
      </svg>
      We accept credit cards
    </p>
  </section>
</main>
</body>
</html>
```